Business Card for Multi-Brand Sportswear Company

We are looking for a business card which represents our company and the multiple brands within it.

The company: Fen Athletics (LTD)
The brands: Fen, TavaPuni, ElmStretch, Grit and Rain

Employees using these cards would be representing Fen Athletics, rather than any of the individual brands. You will see a current design within the uploaded files, to give some inspiration. The actual text of the brands is not necessary, but the logos should be on there is some format.

Our creative minds on this are stretched, so we are looking for someone to make this their own, and show us what a good business card should look like.

We may like to get these printed with spot gloss, so keep that in mind with your designs.

www.fenathletics.co.uk

Industry/Entity Type

Business

Contact Information for Business Card

Leo Pemberton-Hale
Operations Manager
(+44) 1632 960 418
Leo@fenathletics.co.uk
www.fenathletics.co.uk

Font styles to use
Sans Serif
Other font styles liked:
• Eurostile

Colors
ffffff

Requirements
Nice to have
• Dark (black) background

```html
<!DOCTYPE html>
<html lang="en">
<head>
<meta charset="utf-8">
<title>Fen Athletics – Business Card</title>
<link rel="stylesheet" href="https://fonts.googleapis.com/css2?family=Michroma&family=Roboto:wght@400;700&display=swap">
<style>
  :root {
    --backdrop: #2b2b2b;
    --card: #0b0b0c;
    --card-edge: #1a1a1c;
    --red: #e3202a;
    --white: #ffffff;
    --silver: #cfcfd2;
    --muted: #8a8a8e;
  }
  * { box-sizing: border-box; margin: 0; padding: 0; }
  html, body { width: 1200px; height: 900px; overflow: hidden; }
  body {
    background: var(--backdrop);
    font-family: "Roboto", Arial, sans-serif;
    color: var(--white);
    position: relative;
  }
  .card {
    position: absolute;
    left: 270px;
    width: 660px;
    height: 380px;
    background: var(--card);
    border: 1px solid var(--card-edge);
    box-shadow: 0 12px 30px rgba(0,0,0,.55);
    overflow: hidden;
  }
  .card--front { top: 50px; }
  .card--back { top: 470px; }
  .card__lines { position: absolute; inset: 0; width: 100%; height: 100%; }

  .brand-name {
    position: absolute;
    font-family: "Michroma", Arial, sans-serif;
    color: var(--silver);
    white-space: nowrap;
    display: flex;
    align-items: center;
    gap: 12px;
    line-height: 1;
  }
  .brand-name__dot {
    width: 12px; height: 12px;
    background: var(--red);
    flex: none;
  }
  .card--front .brand-name { left: 120px; top: 62px; font-size: 34px; }
  .card--back .brand-name { left: 220px; top: 80px; font-size: 54px; }

  .brand-row {
    position: absolute;
    left: 0; right: 0; top: 262px;
    display: flex; justify-content: center; gap: 34px;
    font-family: "Michroma", Arial, sans-serif;
    font-size: 12px;
    color: var(--muted);
  }
  .site-url {
    position: absolute;
    left: 0; right: 0; top: 296px;
    text-align: center;
    font-weight: 700;
    font-size: 19px;
    color: var(--white);
  }
  .site-url__domain { color: var(--red); }

  .person {
    position: absolute;
    left: 60px; top: 228px;
  }
  .person__name { font-weight: 700; font-size: 21px; }
  .person__role { font-size: 17px; color: var(--red); margin-top: 4px; }

  .divider {
    position: absolute;
    left: 392px; top: 160px;
    width: 1px; height: 88px;
    background: var(--muted);
  }
  .contact {
    position: absolute;
    left: 408px; top: 158px;
    list-style: none;
    font-size: 17px;
  }
  .contact li { display: flex; align-items: center; gap: 8px; height: 30px; white-space: nowrap; }
  .contact svg { width: 14px; height: 14px; flex: none; }

  .address {
    position: absolute;
    left: 220px; top: 318px;
    font-size: 17px;
    color: var(--white);
  }
</style>
</head>
<body>

  <section class="card card--front" aria-label="Card front">
    <svg class="card__lines" viewBox="0 0 660 380" aria-hidden="true">
      <line x1="470" y1="128" x2="660" y2="128" stroke="var(--red)" stroke-width="4"/>
      <polygon points="384,121 476,121 470,135 376,135" fill="var(--white)"/>
      <line x1="0" y1="232" x2="250" y2="232" stroke="var(--red)" stroke-width="4"/>
      <polygon points="250,225 360,225 354,239 244,239" fill="var(--white)"/>
    </svg>
    <div class="brand-name"><span class="brand-name__dot"></span>Fen Athletics</div>
    <div class="brand-row">
      <span>TavaPuni</span><span>Grit and Rain</span><span>ElmStretch</span>
    </div>
    <p class="site-url">www.<span class="site-url__domain">fenathletics</span>.co.uk</p>
  </section>

  <section class="card card--back" aria-label="Card back">
    <svg class="card__lines" viewBox="0 0 660 380" aria-hidden="true">
      <line x1="470" y1="82" x2="660" y2="82" stroke="var(--red)" stroke-width="4"/>
      <polygon points="392,75 476,75 470,89 384,89" fill="var(--white)"/>
      <line x1="0" y1="204" x2="262" y2="204" stroke="var(--red)" stroke-width="4"/>
      <polygon points="262,197 372,197 366,211 256,211" fill="var(--white)"/>
    </svg>
    <div class="brand-name">Fen</div>

    <div class="person">
      <p class="person__name">Leo Pemberton-Hale</p>
      <p class="person__role">Operations Manager</p>
    </div>

    <div class="divider"></div>

    <ul class="contact">
      <li>
        <svg viewBox="0 0 14 14" aria-hidden="true"><circle cx="7" cy="7" r="7" fill="var(--red)"/><path d="M4.5 3.5l1.5 0 .6 2-1 .8a5 5 0 0 0 2.1 2.1l.8-1 2 .6v1.5c0 .5-.5 1-1 1A6 6 0 0 1 3.5 4.5c0-.5.5-1 1-1z" fill="var(--card)"/></svg>
        (+44) 1632 960 418
      </li>
      <li>
        <svg viewBox="0 0 14 14" aria-hidden="true"><circle cx="7" cy="7" r="7" fill="var(--red)"/><rect x="3.5" y="4.5" width="7" height="5" fill="none" stroke="var(--card)" stroke-width="1"/><path d="M3.5 4.5L7 7.3l3.5-2.8" fill="none" stroke="var(--card)" stroke-width="1"/></svg>
        Leo@fenathletics.co.uk
      </li>
      <li>
        <svg viewBox="0 0 14 14" aria-hidden="true"><circle cx="7" cy="7" r="7" fill="var(--red)"/><circle cx="7" cy="7" r="3.5" fill="none" stroke="var(--card)" stroke-width="1"/><line x1="3.5" y1="7" x2="10.5" y2="7" stroke="var(--card)" stroke-width="1"/></svg>
        www.fenathletics.co.uk
      </li>
    </ul>

    <p class="address">Low Meadow, Elmford, Ashby, AB9 4ZX</p>
  </section>

</body>
</html>
```